Building Referrer Relationships Booklet

4 page A4 booklet to give to potential professional referrers to establish a collaborative relationship.Needs to be bright, vibrant, colourful, friendly, inviting, in keeping with The Linden Practice colours.
Want to provide potential referrer partners a great reason to choose to collaborate with us. They need to know who we are, what makes us different/appealing, and who we are looking for to connect with.
The final product should communicate high performance and connectedness.
Updates

Target Market(s)

professional medical allied health and fitness practitioners

Industry/Entity Type

Health

Requirements
Must have
• energetic, vibrant, engaging, inviting, images

```html
<!DOCTYPE html>
<html lang="en">
<head>
<meta charset="utf-8">
<title>The Linden Practice – Referral Partnerships Booklet</title>
<link href="https://fonts.googleapis.com/css2?family=Raleway:ital,wght@0,300;0,400;0,600;0,700;1,700&display=swap" rel="stylesheet">
<style>
:root{
  --yellow:#fcc72e;
  --yellow-soft:#fde07a;
  --slate:#34444f;
  --ink:#2b2b2b;
  --white:#ffffff;
  --bg:#ececec;
}
*{box-sizing:border-box;margin:0;padding:0}
html,body{width:1200px;height:1015px;overflow:hidden;background:var(--bg)}
body{font-family:'Raleway',sans-serif;color:var(--ink);position:relative}
.page{position:absolute;width:360px;height:502px;background:var(--white);overflow:hidden}
.abs{position:absolute}
.chat{position:absolute;width:22px;height:22px;border-radius:50%;background:var(--yellow);display:flex;align-items:center;justify-content:center}
.bar{position:absolute;left:0;right:0;background:var(--yellow);font-weight:700;text-align:center;color:var(--slate)}
.list-title{font-size:6.5px;font-weight:700;letter-spacing:.1px}
.mini-list{list-style:none;font-size:4.8px;line-height:1.25}
.mini-list li{display:flex;align-items:flex-start;gap:3px;margin-bottom:6.4px}
.dot{width:6px;height:6px;border-radius:50%;background:var(--yellow);flex:none}
.dot.dark{background:var(--slate)}
.achievements{left:29px;top:55px;width:146px}
.athletes{left:217px;top:42px;width:135px;color:var(--white)}
.ref-list{list-style:none;position:absolute;left:36px;top:197px;width:300px}
.ref-list li{margin-bottom:5.6px}
.ref-list .role{font-size:9px;font-weight:400;text-transform:uppercase;line-height:1}
.ref-list .role::before{content:"• ";font-size:7px}
.ref-list .desc{font-size:6.5px;font-weight:300;padding-left:22px;line-height:1.3}
.footer{position:absolute;left:0;right:0;bottom:0;background:var(--yellow)}
.logo-slot{text-align:center;color:var(--white)}
.logo-slot b{display:block;font-size:13px;font-weight:700;line-height:1}
.logo-slot span{display:block;font-size:4.5px;letter-spacing:.2px}
.contact{font-size:4.8px;color:var(--ink);display:flex;align-items:center;gap:4px}
.photo{position:absolute}
.num{display:inline-flex;width:9px;height:9px;border-radius:50%;background:var(--yellow);font-size:5.5px;align-items:center;justify-content:center;color:var(--ink);margin-right:4px;vertical-align:middle}
.step{font-size:9.5px;font-weight:400;line-height:1.1;text-transform:uppercase}
.step small{font-size:6px}
.sub{font-size:5.2px;font-weight:300;line-height:1.32;padding-left:49px}
</style>
</head>
<body>

<!-- ============ Inside left: achievements & partners ============ -->
<section class="page" style="left:232px;top:3px">
  <svg class="abs" style="left:0;top:0" width="360" height="175">
    <polygon points="180,0 360,0 360,175 180,175" fill="var(--slate)"/>
    <polygon points="172,0 195,0 180,16" fill="var(--yellow)"/>
  </svg>
  <div class="chat" style="left:170px;top:10px">
    <svg width="12" height="12" viewBox="0 0 12 12"><path d="M6 1.5c-2.8 0-4.5 1.7-4.5 3.8 0 1.2.6 2.2 1.5 2.9L2.5 10.5 5 8.9c.3.1.6.1 1 .1 2.8 0 4.5-1.7 4.5-3.8S8.8 1.5 6 1.5z" fill="none" stroke="#fff" stroke-width=".9"/><circle cx="4" cy="5.3" r=".6" fill="#fff"/><circle cx="6" cy="5.3" r=".6" fill="#fff"/><circle cx="8" cy="5.3" r=".6" fill="#fff"/></svg>
  </div>

  <div class="abs achievements">
    <p class="list-title" style="margin-bottom:10px">OUR TEAM ACHIEVEMENTS:</p>
    <ul class="mini-list">
      <li><i class="dot dark"></i>DIRECTOR, COASTAL SPORTS MEDICINE BOARD (CSMB)</li>
      <li><i class="dot dark"></i>DIRECTOR, PACIFIC COLLEGE OF SPORTS<br>PODIATRY (PCSP)</li>
      <li><i class="dot dark"></i>EXTERNAL ADVISOR, HARBOURSIDE UNIVERSITY<br>PODIATRY UNIT</li>
      <li><i class="dot dark"></i>GROUNDWORK BAREFOOT REHABILITATION INSTRUCTOR</li>
      <li><i class="dot dark"></i>STRIDE MANUAL THERAPIES TRAINED</li>
      <li><i class="dot dark"></i>FASCIA LINES TRAINED</li>
      <li><i class="dot dark"></i>CLASS 3B LASER CERTIFIED</li>
    </ul>
  </div>

  <div class="abs athletes">
    <p class="list-title" style="margin-bottom:10px">OUR ELITE ATHLETE EXPERIENCE:</p>
    <ul class="mini-list">
      <li><i class="dot"></i>NATIONAL PERFORMANCE CENTRE</li>
      <li><i class="dot"></i>NATIONAL RUGBY SQUAD</li>
      <li><i class="dot"></i>SUMMER GAMES SQUAD</li>
      <li><i class="dot"></i>WESTSHORE TRIATHLON CHAMPIONSHIPS</li>
      <li><i class="dot"></i>SOUTHBANK NATIONS GAMES</li>
      <li><i class="dot"></i>RIVERSIDE TENNIS CUP</li>
    </ul>
  </div>

  <div class="bar" style="top:175px;height:16px;font-size:9.5px;line-height:16px">REFERRAL PARTNERS REQUIRED:</div>

  <div class="chat" style="left:319px;top:201px">
    <svg width="12" height="12" viewBox="0 0 12 12"><path d="M6 1.5c-2.8 0-4.5 1.7-4.5 3.8 0 1.2.6 2.2 1.5 2.9L2.5 10.5 5 8.9c.3.1.6.1 1 .1 2.8 0 4.5-1.7 4.5-3.8S8.8 1.5 6 1.5z" fill="none" stroke="#fff" stroke-width=".9"/><circle cx="4" cy="5.3" r=".6" fill="#fff"/><circle cx="6" cy="5.3" r=".6" fill="#fff"/><circle cx="8" cy="5.3" r=".6" fill="#fff"/></svg>
  </div>

  <ul class="ref-list">
    <li><p class="role">Massage therapists</p><p class="desc">Deep tissue and remedial massage<br>Therapeutic massage</p></li>
    <li><p class="role">Fascial therapists</p><p class="desc">Fascia lines releases to reset the alignment of the whole body</p></li>
    <li><p class="role">Physiotherapists</p><p class="desc">Pain relief, protect and strengthen both lower limb and upper limb</p></li>
    <li><p class="role">GP, sports physicians</p><p class="desc">General health, diagnostics, treatment support, prescription medications<br>Specialist referrals</p></li>
    <li><p class="role">Osteopaths and chiropractors</p><p class="desc">Mobilisation and manipulative therapy for the spinal column and limbs</p></li>
    <li><p class="role">Dietician and nutritionists</p><p class="desc">DEXA scan for bone density/lean mass/fat mass<br>Optimising gut health and nutrition - You are what you eat!</p></li>
    <li><p class="role">Psychologists/psychiatrists</p><p class="desc">Sometimes our physical body cannot get better until we optimise a<br>healthy mind</p></li>
    <li><p class="role">Personal trainers, pilates and yoga instructors</p><p class="desc">Create awesome body strength, flexibility and resilience</p></li>
    <li><p class="role">Surgeons</p><p class="desc">When conservative methods are ineffective, surgical intervention works well.</p></li>
  </ul>

  <div class="footer" style="height:53px;display:flex;justify-content:center;align-items:center;gap:20px">
    <div class="logo-slot"><b>LOGO</b><span>SLOGAN HERE</span></div>
    <div class="logo-slot"><b>LOGO</b><span>SLOGAN HERE</span></div>
    <div class="logo-slot"><b>LOGO</b><span>SLOGAN HERE</span></div>
    <div class="logo-slot"><b>LOGO</b><span>SLOGAN HERE</span></div>
    <div class="logo-slot"><b>LOGO</b><span>SLOGAN HERE</span></div>
  </div>
</section>

<!-- ============ Cover ============ -->
<section class="page" style="left:600px;top:3px">
  <div class="photo" role="img" aria-label="Photo of a team stacking hands together" style="left:0;top:0;width:360px;height:240px;background:linear-gradient(135deg,#8a5a3a 0%,#c08a5e 40%,#a56e47 65%,#d8c3a5 100%)"></div>
  <div class="photo" role="img" aria-label="Photo of an athlete stretching, muscles highlighted" style="left:0;top:210px;width:190px;height:240px;background:linear-gradient(160deg,#cfcfcf,#9c9c9c 60%,#7a6a64)"></div>
  <svg class="abs" style="left:0;top:0" width="360" height="450">
    <polygon points="0,170 360,230 360,240 0,190" fill="var(--yellow-soft)"/>
    <polygon points="0,190 360,240 360,258 0,220" fill="var(--yellow)"/>
    <polygon points="180,172 360,228 360,450 180,450" fill="var(--slate)"/>
    <polygon points="0,215 180,250 180,258 0,222" fill="var(--yellow)" opacity=".9"/>
    <polygon points="260,0 360,0 360,40" fill="var(--yellow)"/>
  </svg>
  <h1 class="abs" style="left:21px;top:20px;font-size:22px;font-weight:700;color:var(--white);letter-spacing:.2px">Referral Partnerships</h1>
  <div class="abs" style="left:10px;top:135px;color:var(--white);font-size:8px;line-height:1.25;font-weight:300">
    WE ARE HERE<br>TO HELP OUR CLIENTS<br><b style="font-weight:700;font-size:12px">GET BACK ON THEIR FEET.</b>
  </div>
  <p class="abs" style="left:197px;top:272px;color:var(--white);font-size:21px;font-weight:300;line-height:1.22">BECAUSE<br>TOGETHER<br>WE ACHIEVE<br>MORE</p>

  <div class="footer" style="height:52px">
    <div class="logo-slot abs" style="left:54px;top:13px"><b>LOGO</b><span>SLOGAN HERE</span></div>
    <div class="abs" style="left:119px;top:13px;width:1.5px;height:22px;background:var(--ink)"></div>
    <div class="contact abs" style="left:136px;top:14px"><svg width="8" height="6" viewBox="0 0 8 6"><rect x=".4" y=".4" width="7.2" height="5.2" fill="none" stroke="#2b2b2b" stroke-width=".8"/><path d="M.4.4 4 3.4 7.6.4" fill="none" stroke="#2b2b2b" stroke-width=".8"/></svg>ourmailhere.com</div>
    <div class="contact abs" style="left:136px;top:27px"><svg width="7" height="7" viewBox="0 0 10 10"><path d="M2 .5 4 3 3 4.3c.6 1.3 1.5 2.2 2.8 2.8L7 6l2.5 2-1 1.5C4.5 9.5.5 5.5.5 1.5z" fill="#2b2b2b"/></svg>00 339 55 55 55</div>
    <div class="contact abs" style="left:218px;top:14px"><i class="dot dark" style="width:5px;height:5px"></i>Social Page</div>
    <div class="contact abs" style="left:218px;top:27px"><svg width="6" height="8" viewBox="0 0 6 8"><path d="M3 0a3 3 0 0 0-3 3c0 2.2 3 5 3 5s3-2.8 3-5a3 3 0 0 0-3-3z" fill="#2b2b2b"/><circle cx="3" cy="3" r="1.1" fill="var(--yellow)"/></svg>Adress here Number 123</div>
  </div>
</section>

<!-- ============ About us ============ -->
<section class="page" style="left:232px;top:509px">
  <div class="photo" role="img" aria-label="Photo space for the clinic team" style="left:2px;top:17px;width:351px;height:115px;background:linear-gradient(180deg,#d9d9d9,#c4c4c4)"></div>
  <svg class="abs" style="left:2px;top:17px" width="351" height="115">
    <polygon points="0,0 351,0 351,28 0,65" fill="var(--yellow)" opacity=".85"/>
    <polygon points="0,65 351,28 351,34 0,72" fill="var(--yellow-soft)" opacity=".7"/>
  </svg>
  <h2 class="abs" style="left:27px;top:50px;font-size:16px;font-weight:700;color:var(--white)">About Us:</h2>
  <div class="chat" style="left:320px;top:23px">
    <svg width="12" height="12" viewBox="0 0 12 12"><path d="M6 1.5c-2.8 0-4.5 1.7-4.5 3.8 0 1.2.6 2.2 1.5 2.9L2.5 10.5 5 8.9c.3.1.6.1 1 .1 2.8 0 4.5-1.7 4.5-3.8S8.8 1.5 6 1.5z" fill="none" stroke="#fff" stroke-width=".9"/><circle cx="4" cy="5.3" r=".6" fill="#fff"/><circle cx="6" cy="5.3" r=".6" fill="#fff"/><circle cx="8" cy="5.3" r=".6" fill="#fff"/></svg>
  </div>

  <div class="bar" style="left:2px;right:7px;top:142px;height:12px;font-size:7.5px;line-height:12px">COURAGE INSPIRATION FUN CREATIVE WOW TEAM</div>
  <div class="abs" style="left:31px;top:160px;width:300px;font-size:6.2px;font-weight:300;line-height:1.35;text-transform:uppercase">
    <p><b style="font-weight:700">Courage</b> gives us the strength and confidence to take risks and embrace challenges.</p>
    <p><b style="font-weight:700">Inspiration</b> is our energy, our fuel for success, that life force that feeds us as we grow and develop.</p>
    <p><b style="font-weight:700">Fun</b> generates happiness, and we all function at our best when we are happy.</p>
    <p><b style="font-weight:700">Creativity</b> sets us as an innovative leading-edge business.</p>
    <p><b style="font-weight:700">Wow</b> means being the very best we can be and realise our true potential. We are not your average business, our service is not average, and our people are not average.</p>
    <p><b style="font-weight:700">Team</b> and in particular high-performance team means we perform at our very best. Great teamwork creates unity and we accomplish much more than each of us alone.</p>
  </div>

  <div class="abs" style="left:2px;right:7px;top:265px;height:27px;background:var(--slate);color:var(--white);font-size:9.5px;font-weight:600;text-align:center;line-height:1.3;padding-top:1px">At The Linden Practice, we are passionate about building<br>strong postural foundations, from the feet up.</div>
  <div class="bar" style="left:2px;right:7px;top:298px;height:14px;font-size:7.5px;line-height:14px;font-weight:600;color:var(--ink)">The top 3 things our clients love about us (and hopefully yours will too!):</div>

  <div class="abs" style="left:18px;top:317px;width:330px">
    <p class="step"><span class="num">1</span>Positive energy, enthusiasm and outcomes</p>
    <p class="sub" style="padding-left:29px;margin-bottom:6px">NPS average score &gt;9 out of 10</p>
    <p class="step"><span class="num">2</span>Trusted leader in the practice of podiatric medicine</p>
    <p class="sub" style="padding-left:29px;margin-bottom:6px">established 1999, elite experience, latest high-tech equipment</p>
    <p class="step"><span class="num">3</span>Focus is on strong feet, not just orthotics!</p>
    <p class="sub" style="padding-left:29px">Groundwork Barefoot Technology, Fascia Lines, Stride Manual</p>
  </div>

  <div class="chat" style="left:14px;top:387px;width:18px;height:18px"></div>
  <p class="abs" style="left:34px;top:389px;font-size:9.5px;font-weight:300;background:var(--yellow);padding:0 2px">OUR TEAM:</p>
  <div class="abs" style="left:52px;top:403px;font-size:6.4px;font-weight:700;font-style:italic;line-height:1.3">
    Dr Marcus Ellery (Principal Podiatrist)<br>Dr Hannah Corbett (Senior Podiatrist)<br>Dr Olivia Tran (Podiatrist)<br>Dr Ben Asher (Podiatrist)<br>Clara Winton (Practice Manager)<br>Jess Parlow (Front Office Administrator)
  </div>
  <div class="photo" role="img" aria-label="Black and white photo of a bare foot sole" style="left:255px;top:388px;width:80px;height:68px;background:radial-gradient(ellipse at 50% 55%,#9a9a9a,#3a3a3a 60%,#151515)"></div>

  <div class="footer" style="height:45px">
    <div class="abs" style="left:26px;top:14px;width:1.5px;height:18px;background:var(--ink)"></div>
    <div class="contact abs" style="left:43px;top:13px"><svg width="8" height="6" viewBox="0 0 8 6"><rect x=".4" y=".4" width="7.2" height="5.2" fill="none" stroke="#2b2b2b" stroke-width=".8"/><path d="M.4.4 4 3.4 7.6.4" fill="none" stroke="#2b2b2b" stroke-width=".8"/></svg>ourmailhere.com</div>
    <div class="contact abs" style="left:43px;top:26px"><svg width="7" height="7" viewBox="0 0 10 10"><path d="M2 .5 4 3 3 4.3c.6 1.3 1.5 2.2 2.8 2.8L7 6l2.5 2-1 1.5C4.5 9.5.5 5.5.5 1.5z" fill="#2b2b2b"/></svg>00 339 55 55 55</div>
    <div class="contact abs" style="left:119px;top:13px"><i class="dot dark" style="width:5px;height:5px"></i>Social Page</div>
    <div class="contact abs" style="left:119px;top:26px"><svg width="6" height="8" viewBox="0 0 6 8"><path d="M3 0a3 3 0 0 0-3 3c0 2.2 3 5 3 5s3-2.8 3-5a3 3 0 0 0-3-3z" fill="#2b2b2b"/><circle cx="3" cy="3" r="1.1" fill="var(--yellow)"/></svg>Adress here Number 123</div>
  </div>
</section>

<!-- ============ The Linden Practice way ============ -->
<section class="page" style="left:600px;top:509px">
  <svg class="abs" style="left:0;top:0" width="360" height="132">
    <polygon points="0,16 360,16 360,40 0,55" fill="var(--yellow)"/>
    <polygon points="0,40 360,30 360,131 0,131" fill="var(--slate)"/>
  </svg>
  <div class="chat" style="left:25px;top:39px">
    <svg width="12" height="12" viewBox="0 0 12 12"><path d="M6 1.5c-2.8 0-4.5 1.7-4.5 3.8 0 1.2.6 2.2 1.5 2.9L2.5 10.5 5 8.9c.3.1.6.1 1 .1 2.8 0 4.5-1.7 4.5-3.8S8.8 1.5 6 1.5z" fill="none" stroke="#fff" stroke-width=".9"/><circle cx="4" cy="5.3" r=".6" fill="#fff"/><circle cx="6" cy="5.3" r=".6" fill="#fff"/><circle cx="8" cy="5.3" r=".6" fill="#fff"/></svg>
  </div>
  <h2 class="abs" style="left:0;right:0;top:54px;text-align:center;font-size:15px;font-weight:700;color:var(--white);padding-left:28px">THE LINDEN PRACTICE WAY</h2>
  <p class="abs" style="left:26px;width:300px;top:84px;color:var(--white);font-size:6.5px;font-weight:300;line-height:1.3;text-align:justify">DIRECTOR, COASTAL SPORTS MEDICINE BOARD (CSMB) OUR PATHWAY TO STRENGTHEN POSTURAL FOUNDATIONS, TO CREATE LASTING CHANGES FOR FREEDOM OF MOVEMENT, AND ULTIMATELY KEEP US GOING WELL BEYOND WHAT WE THOUGHT WAS POSSIBLE (UPDATED AS RESEARCH AND TECH CHANGES).</p>

  <div class="bar" style="top:138px;height:11px;font-size:9px;line-height:11px;text-align:left;padding-left:19px;color:var(--slate)">Fix Your Feet</div>
  <div class="abs" style="left:19px;top:154px;width:340px">
    <p class="step"><span class="num">1</span>Fix the pain</p>
    <p class="sub">Provide analgesia<br>Reduce inflammation<br>Corn/callus/foreign body removal<br>Ingrown/thickened toenail repair and maintenance<br>Surgery</p>
    <p class="step" style="margin-top:2px"><span class="num">2</span>Protect the feet <small>(Reduce damage, optimise stability, promote healing)</small></p>
    <p class="sub">Reduce tissue damage<br>Optimise Foot Posture<br>Activate neuromuscular/reflexive balance stability<br>Promote tissue repair/cellular regeneration</p>
    <p class="step" style="margin-top:4px"><span class="num">3</span>Strengthen the feet (increase strength and resilience</p>
    <p class="sub">Strengthen intrinsics<br>Connect foot strength to core strength<br>Stimulate neuromuscular strength</p>
  </div>

  <div class="bar" style="top:288px;height:10px;font-size:9px;line-height:10px;text-align:left;padding-left:19px;color:var(--slate)">Fix Your Feet</div>
  <div class="abs" style="left:19px;top:301px;width:192px">
    <p class="step" style="font-size:8.8px"><span class="num">4</span>Protect the whole body (stability)</p>
    <p class="sub">Optimise Postural Alignment<br>Activate neuromuscular/reflexive balance stability<br>Customised corrective exercises<br>Improve cellular regeneration<br>Optimise nutrition/healthy gut<br>Optimise healthy mind</p>
    <p class="step" style="margin-top:5px"><span class="num">5</span>Strengthen the whole body</p>
    <p class="sub" style="padding-left:32px">(STRENGTH, ELASTICITY)</p>
    <p class="sub">Strengthen the deep core (stabilisers)<br>Strengthen the outer core (mobilisers)<br>Increase fascial elasticity/strength<br>Increase functional strength<br>Increase endurance<br>Customised nutrition for specific performance<br>Improve psychological resilience</p>
    <p class="step" style="margin-top:5px"><span class="num">6</span>Repeat consistently</p>
  </div>

  <div class="footer" style="height:37px">
    <div class="abs" style="left:26px;top:9px;width:1.5px;height:18px;background:var(--ink)"></div>
    <div class="contact abs" style="left:43px;top:8px"><svg width="8" height="6" viewBox="0 0 8 6"><rect x=".4" y=".4" width="7.2" height="5.2" fill="none" stroke="#2b2b2b" stroke-width=".8"/><path d="M.4.4 4 3.4 7.6.4" fill="none" stroke="#2b2b2b" stroke-width=".8"/></svg>ourmailhere.com</div>
    <div class="contact abs" style="left:43px;top:21px"><svg width="7" height="7" viewBox="0 0 10 10"><path d="M2 .5 4 3 3 4.3c.6 1.3 1.5 2.2 2.8 2.8L7 6l2.5 2-1 1.5C4.5 9.5.5 5.5.5 1.5z" fill="#2b2b2b"/></svg>00 339 55 55 55</div>
    <div class="contact abs" style="left:119px;top:8px"><i class="dot dark" style="width:5px;height:5px"></i>Social Page</div>
    <div class="contact abs" style="left:119px;top:21px"><svg width="6" height="8" viewBox="0 0 6 8"><path d="M3 0a3 3 0 0 0-3 3c0 2.2 3 5 3 5s3-2.8 3-5a3 3 0 0 0-3-3z" fill="#2b2b2b"/><circle cx="3" cy="3" r="1.1" fill="var(--yellow)"/></svg>Adress here Number 123</div>
  </div>

  <div class="abs" style="left:212px;top:296px;width:132px;height:201px;background:var(--white);padding:3px;display:grid;grid-template-columns:1fr 1fr;grid-template-rows:1fr 1fr 1fr;gap:3px">
    <div role="img" aria-label="Group photo of the team at a workshop" style="grid-column:1 / 3;background:linear-gradient(135deg,#8c7a70,#c9a793 50%,#7d2e2e)"></div>
    <div role="img" aria-label="Photo of a training session" style="background:linear-gradient(160deg,#a9a9a9,#6f6a66)"></div>
    <div role="img" aria-label="Photo of a group class on a timber floor" style="background:linear-gradient(160deg,#b3a08a,#8d6a4b)"></div>
    <div role="img" aria-label="Photo of practitioners presenting" style="background:linear-gradient(160deg,#c8c2b8,#7b7f86)"></div>
    <div role="img" aria-label="Photo of a movement workshop" style="background:linear-gradient(160deg,#b79a7c,#7f5c3f)"></div>
  </div>
</section>

</body>
</html>
```